Silvermoor Property Development Co.

We need a logo and business card design for a Hong Kong based real estate company, PLX Land. We are want the brand to reflect the owners forward thinking, creative, and trend setting projects, while also reflecting a sense of security and strength. We invest in industrial properties which we convert to co-living or co-working spaces. PLX stands for Greater Bay Area which is the region around southern China including HK, Macau, and 9 other Chinese cities...made up of approx. 68 million people. There are massive infrastructure projects including the bridge to Macau and high-speed rail to SZ and the bridge connecting SZ and Zhongshan.

Target Market(s)

Chinese and western retail investors, as well as institutional investors

Industry/Entity Type

Real Estate Development

Contact Information for Business Card

Dale Whitford
CEO
dale@plxland-example.com
M + 852 9581 4062
F + 852 3864 2217
Suite 2207, The Halvern, 41 Tremont Rd., Central, Hong Kong

Logo Text

plx land (company name) lifestyle property development (underneath)

Colors

Designer to choose colors to be used in the design.

Requirements
Must have
• Details listed above. One side should include the logo and company name...plx land in modern, hip styling with "lifestyle property development"
Nice to have
• Could be a Black card, with metallic purple "plx" and white "land"...but open great design ideas
Should not have
• boring and traditional layout

```html
<!DOCTYPE html>
<html lang="en">
<head>
<meta charset="utf-8">
<title>PLX Land – Business Card</title>
<link rel="stylesheet" href="https://fonts.googleapis.com/css2?family=Exo+2:wght@500;700;800&family=Open+Sans:wght@400&family=Oswald:wght@400&display=swap">
<style>
  :root {
    --backdrop: #9a9a9a;
    --card-light: #ffffff;
    --card-dark: #1f1f1f;
    --gold: #c9980f;
    --ink: #222222;
    --rule: #8a8a8a;
    --tagline: #b9b9b9;
    --skyline-top: #262626;
    --skyline-bottom: #191919;
  }
  * { margin: 0; padding: 0; box-sizing: border-box; }
  html, body { width: 1200px; height: 900px; overflow: hidden; }
  body { background: var(--backdrop); position: relative; font-family: "Open Sans", sans-serif; }

  .card {
    position: absolute;
    top: 275px;
    width: 478px;
    height: 293px;
    box-shadow: 2px 3px 4px rgba(0,0,0,0.35);
    overflow: hidden;
  }
  .card--front {
    left: 120px;
    background: var(--card-light);
    border-radius: 0 55px 0 55px;
  }
  .card--back {
    left: 606px;
    background: var(--card-dark);
    border-radius: 55px 0 55px 0;
  }

  .wordmark {
    position: absolute;
    font-family: "Exo 2", sans-serif;
    font-weight: 800;
    color: var(--gold);
    letter-spacing: 2px;
    white-space: nowrap;
    line-height: 1;
  }
  .card--front .wordmark { right: 26px; top: 62px; font-size: 52px; }
  .card--back .wordmark { left: 0; right: 0; text-align: center; top: 98px; font-size: 48px; }

  .person__name {
    position: absolute; left: 28px; top: 171px;
    font-family: "Exo 2", sans-serif; font-weight: 500;
    font-size: 16px; letter-spacing: 1px; color: var(--gold);
  }
  .person__role {
    position: absolute; left: 28px; top: 189px;
    font-size: 13px; color: var(--ink);
  }
  .person__rule {
    position: absolute; left: 70px; top: 196px;
    width: 384px; height: 1px; background: var(--rule);
  }

  .contact {
    position: absolute; left: 28px; top: 218px;
    list-style: none; font-size: 14px; color: var(--ink); line-height: 17px;
  }
  .contact li { display: flex; align-items: center; gap: 4px; }
  .contact svg { width: 11px; height: 11px; fill: var(--gold); flex: none; }

  .address {
    position: absolute; right: 28px; top: 216px;
    font-style: normal; text-align: right;
    font-size: 14px; color: var(--ink); line-height: 17px;
  }

  .skyline {
    position: absolute; left: 10px; right: 0; top: 95px; bottom: 0;
    background: linear-gradient(180deg, var(--skyline-top), var(--skyline-bottom));
    opacity: 0.8;
  }
  .tagline {
    position: absolute; left: 0; right: 0; top: 182px; text-align: center;
    font-family: "Oswald", sans-serif; font-size: 13px; letter-spacing: 0.6px;
    color: var(--tagline);
  }
</style>
</head>
<body>

  <section class="card card--front" aria-label="Business card front">
    <div class="wordmark">PLX LAND</div>

    <h1 class="person__name">DALE WHITFORD</h1>
    <p class="person__role">CEO</p>
    <div class="person__rule"></div>

    <ul class="contact">
      <li>
        <svg viewBox="0 0 12 12" aria-hidden="true"><path d="M3 0h6a1 1 0 0 1 1 1v10a1 1 0 0 1-1 1H3a1 1 0 0 1-1-1V1a1 1 0 0 1 1-1zm0 1.5v8h6v-8zm3 8.7a.6.6 0 1 0 0 1.2.6.6 0 0 0 0-1.2z"/></svg>
        + 852 9581 4062
      </li>
      <li>
        <svg viewBox="0 0 12 12" aria-hidden="true"><path d="M3 0h6v3H3zM1 4h10a1 1 0 0 1 1 1v4h-2v3H2V9H0V5a1 1 0 0 1 1-1zm2 4v3h6V8z"/></svg>
        + 852 3864 2217
      </li>
      <li>
        <svg viewBox="0 0 12 12" aria-hidden="true"><path d="M0 2h12v1L6 7 0 3zm0 2.3 6 4 6-4V10H0z"/></svg>
        dale@plxland-example.com
      </li>
    </ul>

    <address class="address">
      Suite 2207, The Halvern<br>
      41 Tremont Rd<br>
      Central, Hong Kong
    </address>
  </section>

  <section class="card card--back" aria-label="Business card back">
    <div class="skyline" role="img" aria-label="Dark city skyline silhouette across the lower card"></div>
    <div class="wordmark">PLX LAND</div>
    <p class="tagline">LIFESTYLE PROPERTY DEVELOPMENT</p>
  </section>

</body>
</html>
```